Bright Pelvicare Business Card

Need a business card for a surgical practice called Bright Pelvicare. We have recently selected a logo (attached). The business card will need to have two formats:
1) One with the logo/physician name/ contact info on the front and location information on the back.
2) One in "appointment reminder card" style with the logo/ contact info/ date/ time on the front and the location information on the back.

The front side should include the following information:
- Logo
- Rohan K. Desai, MD FACOG
- phone: 469-555-0182
- fax: 1-469-555-0317
- email: admin@brightpelvi.com
- website: www.brightpelvicare.com

The back side should have the office locations listed:
4518 Kestrel Ave, Plano, TX 75198
3920 Bramwell Rd, Plano, TX 75147
2245 Silverpine Ln, Irving, TX 75163
815 W Garnet Ave S310, Dallas, TX 75284
3614 Lantern Blvd, Grand Prairie, TX 75179
7405 Amberly Crest Dr, San Antonio, TX 78391
5812 Tolliver Rd, Pasadena, TX 77639

Target Market(s)

1. Other physicians who might refer patients
2. Female patients

Industry/Entity Type

Business

Font styles to use
Other font styles liked:
• Tahoma for lettering

Requirements
Must have
• As per the instructions
Should not have
• No other images needed -- please try to keep font consistent with logo design. Can use Tahoma as the font for lettering.

```html
<!DOCTYPE html>
<html lang="en">
<head>
<meta charset="utf-8">
<title>Bright Pelvicare Business Card</title>
<link href="https://fonts.googleapis.com/css2?family=Lato:wght@400;700&display=swap" rel="stylesheet">
<style>
  :root {
    --backdrop: #ececec;
    --card: #ffffff;
    --brand-blue: #2a64a8;
    --ink: #1f1f1f;
    --art-light: #8b95c9;
    --art-dark: #3b7db6;
  }
  * { box-sizing: border-box; margin: 0; padding: 0; }
  html, body {
    width: 1200px; height: 720px; overflow: hidden;
    background: var(--backdrop);
    font-family: "Lato", Tahoma, sans-serif;
  }
  .canvas { position: relative; width: 1200px; height: 720px; }
  .card {
    position: absolute; top: 241px;
    width: 420px; height: 240px;
    background: var(--card);
    overflow: hidden;
  }
  .card--front { left: 147px; }
  .card--back { left: 633px; }

  .brand-name {
    position: absolute; left: 27px; top: 66px;
    font-size: 17px; font-weight: 700;
    color: var(--brand-blue); letter-spacing: 0.2px;
  }
  .brand-mark {
    position: absolute; left: 107px; top: 26px;
    width: 32px; height: 32px; border-radius: 50%;
    background: var(--brand-blue);
  }
  .physician { position: absolute; left: 27px; top: 105px; }
  .physician__name { font-size: 13.5px; font-weight: 700; color: var(--brand-blue); }
  .physician__title { font-size: 9.5px; color: var(--ink); margin-top: 1px; }

  .contact-list {
    position: absolute; left: 27px; top: 156px;
    list-style: none; font-size: 9.8px; color: var(--ink);
  }
  .contact-list li { display: flex; align-items: center; height: 12.8px; }
  .contact-list svg { width: 10px; height: 10px; margin-right: 8px; fill: var(--brand-blue); }

  .portrait-art {
    position: absolute; top: 0; height: 240px;
    background: linear-gradient(90deg, var(--art-light), var(--art-dark));
  }
  .card--front .portrait-art {
    left: 296px; width: 124px;
    border-radius: 60px 0 0 70px;
  }
  .card--back .portrait-art {
    left: 0; width: 116px;
    background: linear-gradient(90deg, var(--art-dark), var(--art-light));
    border-radius: 0 56px 66px 0;
  }

  .locations {
    position: absolute; right: 17px; top: 60px;
    text-align: right; color: var(--ink);
    font-size: 12.4px; line-height: 16px;
    white-space: nowrap;
  }
  .locations__title { font-weight: 700; color: var(--brand-blue); font-size: 12.8px; }
  .locations ul { list-style: none; }
</style>
</head>
<body>
<div class="canvas">

  <section class="card card--front">
    <div class="brand-mark"></div>
    <div class="brand-name">Bright Pelvicare</div>

    <div class="physician">
      <div class="physician__name">Rohan K. Desai</div>
      <div class="physician__title">MD FACOG</div>
    </div>

    <ul class="contact-list">
      <li>
        <svg viewBox="0 0 10 10"><path d="M1 3.5 C1 1.5 3 1 5 1 C7 1 9 1.5 9 3.5 L7 3.5 L6.5 2.5 L3.5 2.5 L3 3.5 Z M2 5 L8 5 L9 9 L1 9 Z"/></svg>
        469-555-0182
      </li>
      <li>
        <svg viewBox="0 0 10 10"><path d="M2.5 1 H7.5 V3.5 H2.5 Z M0.5 4 H9.5 V7.5 H8 V6 H2 V7.5 H0.5 Z M2.5 6.5 H7.5 V9 H2.5 Z"/></svg>
        1-469-555-0317
      </li>
      <li>
        <svg viewBox="0 0 10 10"><path d="M0.5 2 H9.5 V8 H0.5 Z" /><path d="M0.8 2.3 L5 5.6 L9.2 2.3" stroke="#fff" stroke-width="0.9" fill="none"/></svg>
        admin@brightpelvi.com
      </li>
      <li>
        <svg viewBox="0 0 10 10"><path d="M0.5 1.5 H9.5 V7 H0.5 Z M1.5 2.5 V6 H8.5 V2.5 Z M3 8 H7 V9 H3 Z"/></svg>
        www.brightpelvicare.com
      </li>
    </ul>

    <div class="portrait-art" role="img" aria-label="Blue gradient profile silhouette of a woman's head"></div>
  </section>

  <section class="card card--back">
    <div class="portrait-art" role="img" aria-label="Blue gradient profile silhouette of a woman's head, mirrored"></div>

    <div class="locations">
      <div class="locations__title">Office locations :</div>
      <ul>
        <li>4518 Kestrel Ave, Plano, TX 75198</li>
        <li>3920 Bramwell Rd, Plano, TX 75147</li>
        <li>2245 Silverpine Ln, Irving, TX 75163</li>
        <li>815 W Garnet Ave S310, Dallas, TX 75284</li>
        <li>3614 Lantern Blvd, Grand Prairie, TX 75179</li>
        <li>7405 Amberly Crest Dr, San Antonio, TX 78391</li>
        <li>5812 Tolliver Rd, Pasadena, TX 77639</li>
      </ul>
    </div>
  </section>

</div>
</body>
</html>
```